I need a business card design for a real estate finance, development and management business. We deal with high net worth clients and ask that the business card be neat, clean and sophisticated. We like the attached logo design, font and color and want to incorporate all this into the business card.

Industry/Entity Type

Real Estate

```html
<!DOCTYPE html>
<html lang="en">
<head>
<meta charset="utf-8">
<title>Silver Harbor – Business Card</title>
<link rel="stylesheet" href="https://fonts.googleapis.com/css2?family=Ubuntu:wght@400;500;700&display=swap">
<style>
  :root {
    --brand-blue: #1f5b9c;
    --paper: #ffffff;
    --backdrop: #e8e8e8;
    --card-shadow: rgba(0, 0, 0, 0.14);
  }
  * { box-sizing: border-box; margin: 0; padding: 0; }
  html, body {
    width: 1200px; height: 947px; overflow: hidden;
    background: var(--backdrop);
    font-family: "Ubuntu", sans-serif;
    color: var(--brand-blue);
  }
  .stage { position: relative; width: 1200px; height: 947px; }
  .card {
    position: absolute; top: 323px;
    width: 525px; height: 300px;
    background: var(--paper);
    box-shadow: 0 6px 18px var(--card-shadow);
    overflow: hidden;
  }
  .card--front { left: 50px; }
  .card--back { left: 625px; }
  .band {
    position: absolute; left: 0; right: 0; height: 15px;
    background: var(--brand-blue);
  }
  .band--top { top: 0; }
  .band--bottom { bottom: 0; }

  .wordmark {
    position: absolute; left: 0; right: 0;
    display: flex; align-items: center; justify-content: center; gap: 12px;
    font-weight: 500; letter-spacing: 0.08em; text-transform: uppercase;
    color: var(--brand-blue);
  }
  .wordmark__square { width: 10px; height: 10px; background: var(--brand-blue); }
  .card--back .wordmark { top: 126px; font-size: 40px; }
  .card--back .wordmark__square { width: 14px; height: 14px; }
  .card--front .wordmark { top: 40px; font-size: 28px; }

  .divider {
    position: absolute; left: 0; right: 0; top: 104px;
    height: 2px; background: var(--brand-blue);
  }
  .person {
    position: absolute; left: 0; right: 0; top: 124px;
    text-align: center;
  }
  .person__name { font-size: 21px; font-weight: 700; letter-spacing: 0.01em; }
  .person__title { font-size: 14px; margin-top: 3px; }

  .contacts {
    position: absolute; left: 20px; right: 20px; top: 196px;
    display: grid; grid-template-columns: 1.1fr 0.8fr 1.6fr; gap: 14px;
    font-size: 13px; line-height: 1.35;
  }
  .contact__icon { width: 16px; height: 16px; display: block; margin-bottom: 5px; }
  .contact__icon path, .contact__icon rect { fill: var(--brand-blue); }
</style>
</head>
<body>
<main class="stage">

  <section class="card card--front" aria-label="Card front">
    <div class="band band--top"></div>
    <div class="wordmark"><span class="wordmark__square"></span>Silver Harbor</div>
    <div class="divider"></div>
    <div class="person">
      <p class="person__name">Daniel R. Whitford</p>
      <p class="person__title">Managing Partner</p>
    </div>
    <div class="contacts">
      <div class="contact contact--address">
        <svg class="contact__icon" viewBox="0 0 16 16" aria-hidden="true"><path d="M8 1 1 7.5h2V15h4v-4h2v4h4V7.5h2z"/></svg>
        <p>58 Harbor Crest<br>Ave. Milford, CT 06460</p>
      </div>
      <div class="contact contact--phone">
        <svg class="contact__icon" viewBox="0 0 16 16" aria-hidden="true"><path d="M2 5c0-2 1.5-3 6-3s6 1 6 3v1h-3.5V4.5h-5V6H2zM4 7h8l2 4v3H2v-3zm4 1.5a2 2 0 1 0 0 4 2 2 0 0 0 0-4z"/></svg>
        <p>555 204 7731</p>
      </div>
      <div class="contact contact--web">
        <svg class="contact__icon" viewBox="0 0 16 16" aria-hidden="true"><path d="M1 2h14v9H1zm1.5 1.5v6h11v-6zM6 12h4l.8 2H5.2z"/></svg>
        <p>drwhitford@silverharborcapital.net<br>www.silverharborcapital.net</p>
      </div>
    </div>
    <div class="band band--bottom"></div>
  </section>

  <section class="card card--back" aria-label="Card back">
    <div class="band band--top"></div>
    <div class="wordmark"><span class="wordmark__square"></span>Silver Harbor</div>
    <div class="band band--bottom"></div>
  </section>

</main>
</body>
</html>
```